Business card for a Exhibition booth fabrication company

Hi. My company would like to change our corporate name card. We are an events and Exhibition stand builder company. We would like our corporate name card to resonate what we do. I need someone to create something unique that relates to the industry that I am in. The graphic designer should be creative to incorporate the elements of my industry and try to blend in well in the design of the card. Our aim is to ensure that we are unique and our card can look different from our competitors.
Updates

Target Market(s)

Marketing and events manager from all companies

Contact Information for Business Card

The business card should have the following details:
Name
Job Title
Email
Website

Colors

Designer to choose colors to be used in the design.

Requirements
Must have
• The card must be look something that is relevant to the service that I am providing. My website is: www.velmora-buildworks.com
• You can see my website to get more information on what service that I am doing
Nice to have
• On the back of my card, I would like to have a globe image with the incorporation of my company logo. This is to indicate that my services can be done in any part of the world.

```html
<!DOCTYPE html>
<html lang="en">
<head>
<meta charset="utf-8">
<title>Velmora Buildworks — Business Card</title>
<link rel="stylesheet" href="https://fonts.googleapis.com/css2?family=Jost:wght@400;500;600&family=Oswald:wght@500&display=swap">
<style>
  :root {
    --bg: #3a3a3c;
    --red: #d3262f;
    --red-deep: #9a1219;
    --map-tone: rgba(255, 120, 125, 0.32);
    --map-fade: rgba(255, 120, 125, 0);
    --black-card: #0b0b0c;
    --white: #ffffff;
    --grey-text: #9a9a9c;
    --accent: #e5232d;
  }
  * { box-sizing: border-box; margin: 0; padding: 0; }
  html, body {
    width: 1200px; height: 1000px; overflow: hidden;
    background: var(--bg);
    font-family: "Jost", sans-serif;
  }
  .canvas { position: relative; width: 1200px; height: 1000px; }

  .card {
    position: absolute;
    width: 640px; height: 366px;
    border-radius: 26px;
    overflow: hidden;
    left: 280px;
  }

  /* Front */
  .card-front {
    top: 70px;
    background: linear-gradient(135deg, var(--red) 0%, var(--red-deep) 100%);
  }
  .world-map-area {
    position: absolute; inset: 0;
    background:
      radial-gradient(ellipse 62% 58% at 48% 46%, var(--map-tone) 0%, rgba(255,120,125,0.18) 55%, var(--map-fade) 100%);
  }
  .brand-lockup {
    position: absolute; left: 0; right: 0; top: 150px;
    display: flex; align-items: center; justify-content: center; gap: 14px;
  }
  .brand-dot { width: 14px; height: 14px; border-radius: 50%; background: var(--white); }
  .brand-name {
    color: var(--white); font-weight: 500; font-size: 31px; letter-spacing: 2.5px;
  }
  .front-website {
    position: absolute; left: 0; right: 0; top: 286px; text-align: center;
    color: var(--white); font-weight: 600; font-size: 17px; letter-spacing: 0.3px;
  }

  /* Back */
  .card-back {
    top: 530px;
    background: var(--black-card);
  }
  .identity {
    position: absolute; right: 400px; top: 128px; text-align: right;
  }
  .person-name {
    font-family: "Oswald", sans-serif; font-weight: 500;
    color: var(--accent); font-size: 32px; letter-spacing: 0.5px; line-height: 1.1;
  }
  .person-title { color: var(--grey-text); font-size: 19px; margin-top: 2px; }
  .divider {
    position: absolute; left: 256px; top: 114px; width: 2px; height: 136px;
    background: var(--accent);
  }
  .contacts {
    position: absolute; left: 276px; top: 112px;
    font-size: 17px; line-height: 1.22; color: var(--grey-text);
  }
  .contact-label { color: var(--accent); font-weight: 500; font-size: 16px; }
  .contact-row { display: flex; align-items: center; gap: 6px; }
  .contact-row svg { width: 16px; height: 16px; flex: none; }
  .web-highlight { color: var(--accent); font-weight: 500; }
</style>
</head>
<body>
<main class="canvas">

  <section class="card card-front">
    <div class="world-map-area" role="img" aria-label="Faint world map spanning the card with a fine grid, showing the company builds exhibition stands anywhere in the world"></div>
    <div class="brand-lockup">
      <span class="brand-dot"></span>
      <span class="brand-name">VELMORA BUILDWORKS</span>
    </div>
    <p class="front-website">www.velmora-buildworks.com</p>
  </section>

  <section class="card card-back">
    <div class="identity">
      <p class="person-name">ADRIAN KESSLER</p>
      <p class="person-title">President</p>
    </div>
    <div class="divider"></div>
    <div class="contacts">
      <p class="contact-label">Singapore Contact:</p>
      <p>+65 84172290</p>
      <p class="contact-label">Qatar Contact:</p>
      <p>+974 55218840</p>
      <p class="contact-row">
        <svg viewBox="0 0 16 16" aria-hidden="true"><rect x="1" y="3" width="14" height="10" rx="1.5" fill="var(--accent)"/><path d="M1.5 4 L8 9 L14.5 4" stroke="var(--black-card)" stroke-width="1.4" fill="none"/></svg>
        info@velmora-buildworks.com
      </p>
      <p class="contact-row">
        <svg viewBox="0 0 16 16" aria-hidden="true"><circle cx="8" cy="8" r="7" fill="var(--accent)"/><g stroke="var(--black-card)" stroke-width="1" fill="none"><ellipse cx="8" cy="8" rx="3" ry="7"/><line x1="1" y1="8" x2="15" y2="8"/><line x1="2.5" y1="4.5" x2="13.5" y2="4.5"/><line x1="2.5" y1="11.5" x2="13.5" y2="11.5"/></g></svg>
        <span>www.<span class="web-highlight">velmora-buildworks</span>.com</span>
      </p>
    </div>
  </section>

</main>
</body>
</html>
```